I have a logo and need to design the business card and stationery.
Updates

The uploaded logo image named as GREYMARSH CONSTRUCTION which is to be replaced to GREYMARSH CONTRACTS. Kindly add below details and submit the designs- Company name- Greymarsh Engineering Contracts LLP Name & Post- Kelvan Joshi (Designated Partner) Address- Block No.317, Wing C, Tulvo Trade Court, Manek Pural Road, Ruparel Industrial Estate, Goregaon(E), Mumbai - 400 063 Contact- +91 97415 60382 Email- kelvanjoshi@mailbrook.example Website- www.greymarshcontracts.example Contact for Letterhead- +91-22-28754193

Hi Tovin Rahul, We are liking your Design #28860835. We have suggested some changes which are mentioned in feedback. Kindly revert with it asap to finalize this design.

Colors

Designer to choose colors to be used in the design.

```html
<!DOCTYPE html>
<html lang="en">
<head>
<meta charset="utf-8">
<title>Greymarsh Contracts – Stationery Set</title>
<link rel="stylesheet" href="https://fonts.googleapis.com/css2?family=Questrial&family=Montserrat:wght@600&display=swap">
<style>
  :root{
    --backdrop:#3b3b3d;
    --paper:#ffffff;
    --ink:#333333;
    --ink-soft:#555555;
    --mark:#3c3c3c;
    --ghost:#efefef;
    --sig-fill:#e6e6e6;
  }
  *{margin:0;padding:0;box-sizing:border-box}
  html,body{width:1200px;height:800px;overflow:hidden;background:var(--backdrop)}
  body{position:relative;font-family:"Questrial",sans-serif;color:var(--ink)}
  .sheet{position:absolute;background:var(--paper);overflow:hidden}
  .abs{position:absolute}
  .brand-square{position:absolute;background:var(--mark)}
  .ghost-square{position:absolute;background:var(--ghost)}
  .brand-name{position:absolute;text-align:center;color:var(--ink);font-family:"Questrial",sans-serif;font-weight:400;line-height:1}
  .brand-name .line1{display:block;letter-spacing:.04em}
  .brand-name .line2{display:block;letter-spacing:.42em}
  .icon{display:inline-block;vertical-align:middle;margin-right:3px}

  /* business card front */
  .card-front{left:99px;top:57px;width:206px;height:123px}
  .card-front .tab{left:0;top:17px;width:19px;height:14px;background:var(--ink)}
  .card-front .person{left:22px;top:15px;font-size:9px;line-height:1}
  .card-front .person b{font-family:"Montserrat",sans-serif;font-weight:600}
  .card-front .role{left:22px;top:25px;font-size:4.6px;color:var(--ink-soft)}
  .card-front .brand-name{left:126px;top:18px;width:72px}
  .card-front .brand-name .line1{font-size:7px}
  .card-front .brand-name .line2{font-size:3.6px;margin-top:1px}
  .card-front .contacts{left:22px;top:94px;font-size:5px;line-height:7.8px;color:var(--ink-soft)}

  /* business card back */
  .card-back{left:371px;top:57px;width:206px;height:123px}
  .card-back .brand-name{left:0;top:60px;width:206px}
  .card-back .brand-name .line1{font-size:10.5px}
  .card-back .brand-name .line2{font-size:5px;margin-top:1.5px}
  .card-back .pin{left:97px;top:81px}
  .card-back .address{left:0;top:91px;width:206px;text-align:center;font-size:4.2px;line-height:5.4px;color:var(--ink-soft)}

  /* envelope */
  .envelope{left:99px;top:232px;width:477px;height:239px}
  .envelope .flap{left:0;top:0;width:477px;height:56px;background:var(--ink);border-radius:0 0 22px 22px}
  .envelope .flap .brand-name{left:0;top:21px;width:477px;color:var(--paper);font-size:10px;letter-spacing:.08em}

  /* compliment sheet */
  .compliment{left:99px;top:505px;width:477px;height:239px}
  .compliment .brand-name{left:15px;top:60px;width:114px}
  .compliment .brand-name .line1{font-size:11.5px}
  .compliment .brand-name .line2{font-size:5.6px;margin-top:1.5px}
  .compliment .address{left:16px;top:191px;font-size:6.2px;line-height:9.2px;color:var(--ink-soft)}
  .compliment .address p{padding-left:8px}

  /* letterhead */
  .letterhead{left:611px;top:57px;width:490px;height:687px}
  .letterhead .brand-name{left:39px;top:90px;width:114px}
  .letterhead .brand-name .line1{font-size:11.5px}
  .letterhead .brand-name .line2{font-size:5.6px;margin-top:1.5px}
  .letterhead .contact-block{left:343px;top:73px;height:34px;border-left:1px solid var(--ink);padding-left:5px;font-size:6.6px;line-height:9.7px;color:var(--ink-soft)}
  .letterhead .salutation{left:39px;top:175px;font-size:12px}
  .letterhead .body-copy{left:39px;width:412px;font-size:8.5px;line-height:9.65px;text-align:justify;color:var(--ink-soft)}
  .letterhead .signature{left:39px;top:453px;width:96px;height:61px;background:var(--sig-fill)}
  .letterhead .sign-role{left:39px;top:521px;font-size:10px;color:var(--ink-soft)}
  .letterhead .address{left:39px;top:622px;font-size:6.3px;line-height:9.8px;color:var(--ink-soft)}
  .letterhead .address p{padding-left:9px}
</style>
</head>
<body>

<!-- Business card: front -->
<section class="sheet card-front" aria-label="Business card front">
  <div class="abs tab"></div>
  <p class="abs person"><b>Kelvan</b> Joshi</p>
  <p class="abs role">(Designated Partner)</p>
  <div class="brand-name"><span class="line1">GREYMARSH</span><span class="line2">CONTRACTS</span></div>
  <div class="ghost-square" style="left:129px;top:52px;width:63px;height:63px"></div>
  <div class="abs contacts">
    <p><svg class="icon" width="5" height="5" viewBox="0 0 10 10"><circle cx="5" cy="5" r="5" fill="#333"/><path d="M3 2.6l1 1.2-.6.6c.4.9 1 1.5 1.9 1.9l.6-.6 1.2 1-.8.9C4.8 7.4 2.6 5.2 2.3 3.4z" fill="#fff"/></svg>+91 97415 60382</p>
    <p><svg class="icon" width="5" height="5" viewBox="0 0 10 10"><circle cx="5" cy="5" r="5" fill="#333"/><rect x="2.5" y="3.3" width="5" height="3.4" fill="#fff"/></svg>kelvanjoshi@mailbrook.example</p>
    <p><svg class="icon" width="5" height="5" viewBox="0 0 10 10"><circle cx="5" cy="5" r="5" fill="#333"/><circle cx="5" cy="5" r="2.6" fill="none" stroke="#fff" stroke-width=".8"/><path d="M2.4 5h5.2M5 2.4v5.2" stroke="#fff" stroke-width=".6"/></svg>www.greymarshcontracts.example</p>
  </div>
</section>

<!-- Business card: back -->
<section class="sheet card-back" aria-label="Business card back">
  <div class="brand-square" style="left:89px;top:25px;width:28px;height:28px"></div>
  <div class="brand-name"><span class="line1">GREYMARSH</span><span class="line2">CONTRACTS</span></div>
  <svg class="abs pin" width="7" height="8" viewBox="0 0 10 12"><path d="M5 .5a4 4 0 0 1 4 4c0 3-4 6.5-4 6.5S1 7.5 1 4.5a4 4 0 0 1 4-4z" fill="none" stroke="#333" stroke-width="1.3"/><circle cx="5" cy="4.5" r="1.4" fill="#333"/></svg>
  <p class="abs address">Block No.317, Wing C, Tulvo Trade Court, Manek Pural Road, Ruparel Industrial Estate,<br>Goregaon(E), Mumbai - 400 063</p>
</section>

<!-- Envelope -->
<section class="sheet envelope" aria-label="Envelope">
  <div class="abs flap">
    <div class="brand-name">GREYMARSH CONTRACTS</div>
  </div>
</section>

<!-- Compliment sheet -->
<section class="sheet compliment" aria-label="Compliment sheet">
  <div class="brand-square" style="left:103px;top:15px;width:35px;height:35px"></div>
  <div class="brand-name"><span class="line1">GREYMARSH</span><span class="line2">CONTRACTS</span></div>
  <div class="ghost-square" style="left:376px;top:140px;width:80px;height:80px"></div>
  <div class="abs address">
    <svg class="abs" style="left:0;top:1px" width="6" height="7" viewBox="0 0 10 12"><path d="M5 .5a4 4 0 0 1 4 4c0 3-4 6.5-4 6.5S1 7.5 1 4.5a4 4 0 0 1 4-4z" fill="none" stroke="#333" stroke-width="1.4"/><circle cx="5" cy="4.5" r="1.4" fill="#333"/></svg>
    <p>Block No.317, Wing C, Tulvo Trade Court,</p>
    <p>Manek Pural Road, Ruparel Industrial Estate,</p>
    <p>Goregaon(E), Mumbai - 400 063</p>
  </div>
</section>

<!-- Letterhead -->
<section class="sheet letterhead" aria-label="Letterhead">
  <div class="brand-square" style="left:78px;top:49px;width:35px;height:35px"></div>
  <div class="brand-name"><span class="line1">GREYMARSH</span><span class="line2">CONTRACTS</span></div>

  <div class="abs contact-block">
    <p><svg class="icon" width="6" height="6" viewBox="0 0 10 10"><circle cx="5" cy="5" r="5" fill="#333"/><path d="M3 2.6l1 1.2-.6.6c.4.9 1 1.5 1.9 1.9l.6-.6 1.2 1-.8.9C4.8 7.4 2.6 5.2 2.3 3.4z" fill="#fff"/></svg>+91-22-28754193</p>
    <p><svg class="icon" width="6" height="6" viewBox="0 0 10 10"><circle cx="5" cy="5" r="5" fill="#333"/><rect x="2.5" y="3.3" width="5" height="3.4" fill="#fff"/></svg>kelvanjoshi@mailbrook.example</p>
    <p><svg class="icon" width="6" height="6" viewBox="0 0 10 10"><circle cx="5" cy="5" r="5" fill="#333"/><circle cx="5" cy="5" r="2.6" fill="none" stroke="#fff" stroke-width=".8"/><path d="M2.4 5h5.2M5 2.4v5.2" stroke="#fff" stroke-width=".6"/></svg>www.greymarshcontracts.example</p>
  </div>

  <p class="abs salutation">Dear Mr.Kelvan</p>

  <p class="abs body-copy" style="top:203px">Lorem ipsum dolor sit amet, consectetuer adipiscing elit, sed diam nonummy nibh euismod tincidunt ut laoreet dolore magna aliquam erat volutpat. Ut wisi enim ad minim veniam, quis nostrud exerci tation ullamcorper suscipit lobortis nisl ut aliquip ex ea commodo consequat. Duis autem vel eum iriure dolor in hendrerit in vulputate velit esse molestie consequat, vel illum dolore eu feugiat nulla facilisis at vero eros et accumsan et iusto odio dignissim qui blandit praesent luptatum zzril delenit augue duis dolore te feugait nulla facilisi.</p>

  <p class="abs body-copy" style="top:270px">Lorem ipsum dolor sit amet, cons ectetuer adipiscing elit, sed diam nonummy nibh euismod tincidunt ut laoreet dolore magna aliquam erat volutpat. Ut wisi enim ad minim veniam, quis nostrud exerci tation ullamcorper suscipit lobortis nisl ut aliquip ex ea commodo consequat.<br>Lorem ipsum dolor sit amet, consectetuer adipiscing elit, sed diam nonummy nibh euismod tincidunt ut laoreet dolore magna aliquam erat</p>

  <p class="abs body-copy" style="top:337px">Lorem ipsum dolor sit amet, cons ectetuer adipiscing elit, sed diam nonummy nibh euismod tincidunt ut laoreet dolore magna aliquam erat volutpat. Ut wisi enim ad minim veniam, quis nostrud exerci tation ullamcorper suscipit lobortis nisl ut aliquip ex ea commodo consequat. Lorem ipsum dolor sit zamet, consectetuer adipiscing elit, sed diam nonummy nibh euismod tincidunt ut laoreet dolore magna aliquam erat volutpat. Ut wisi enim ad minim veniam, quis nostrud exerci tation ullamcorper suscipit lobortis nisl ut aliquip ex ea commodo consequat. Duis autem vel eum iriure dolor in hendrerit in vulputate velit esse molestie consequat, vel illum dolore eu feugiat nulla facilisis at vero eros et accumsan et iusto odio dignissim qui blandit praesent luptatum zzril delenit augue duis dolore te feugait nulla facilisi. Lorem ipsum dolor sit amet, cons ectetuer adipiscing elit, sed diam nonummy nibh euismod tincidunt ut laoreet dolore magna aliquam erat volutpat. Ut wisi enim ad minim veniam, quis nostrud exerci tation ullamcorper suscipit lobortis nisl ut aliquip ex ea commodo consequat.</p>

  <div class="abs signature" role="img" aria-label="Handwritten signature of the Managing Director"></div>
  <p class="abs sign-role">Managing Director</p>

  <div class="ghost-square" style="left:304px;top:512px;width:147px;height:147px"></div>

  <div class="abs address">
    <svg class="abs" style="left:0;top:1px" width="6" height="7" viewBox="0 0 10 12"><path d="M5 .5a4 4 0 0 1 4 4c0 3-4 6.5-4 6.5S1 7.5 1 4.5a4 4 0 0 1 4-4z" fill="none" stroke="#333" stroke-width="1.4"/><circle cx="5" cy="4.5" r="1.4" fill="#333"/></svg>
    <p>Block No.317, Wing C, Tulvo Trade Court,</p>
    <p>Manek Pural Road, Ruparel Industrial Estate,</p>
    <p>Goregaon(E), Mumbai - 400 063</p>
  </div>
</section>

</body>
</html>
```